Brindle Water - 500ml

to create a water bottle packaging similar to L'onde Claire design. Bottle should be blue similar to PURE FLOW but change the design/logo to Brindle. Wording should be similar just different design and logo. Thanks.

Colors
0054AA
0677BA
7BADD7
CADEEF
E8F1F8

Requirements
Must have
• Bottle must not be in plastic bottles. They are made in a carton instead - see PURE FLOW for reference.

```html
<!DOCTYPE html>
<html lang="en">
<head>
<meta charset="utf-8">
<title>Brindle Water 500ml – Carton Colour Options</title>
<link rel="stylesheet" href="https://fonts.googleapis.com/css2?family=Montserrat:wght@300;400;500;600;700;800&family=Kaushan+Script&display=swap">
<style>
  :root {
    --deep-blue: #0d3a78;
    --cyan-blue: #0ba2e2;
    --white: #ffffff;
    --backdrop: #f1f1f2;
    --cap: #f4f4f4;
    --cap-edge: #dcdcdc;
    --shoulder: #fafafa;
  }
  * { margin: 0; padding: 0; box-sizing: border-box; }
  html, body { width: 1200px; height: 1007px; overflow: hidden; }
  body {
    position: relative;
    background: var(--backdrop);
    font-family: "Montserrat", sans-serif;
    color: var(--white);
  }

  .carton { position: absolute; top: 33px; width: 240px; height: 798px; }
  .carton--deep { left: 252px; --panel: var(--deep-blue); }
  .carton--cyan { left: 705px; --panel: var(--cyan-blue); }

  .carton__cap {
    position: absolute; left: 48px; top: 0; width: 144px; height: 62px;
    background: var(--cap); border: 1px solid var(--cap-edge); border-radius: 8px 8px 2px 2px;
  }
  .carton__shoulder {
    position: absolute; left: 0; top: 62px; width: 240px; height: 69px;
    background: var(--shoulder); border: 1px solid var(--cap-edge); border-bottom: none;
  }
  .carton__panel {
    position: absolute; left: 0; top: 131px; width: 240px; height: 667px;
    background: var(--panel); border-radius: 0 0 8px 8px; text-align: center;
  }
  .carton__panel > * { position: absolute; left: 0; width: 100%; }

  .tagline { top: 42px; font-size: 13px; font-weight: 500; letter-spacing: 0.06em; }
  .brand-name { top: 106px; font-size: 54px; font-weight: 700; line-height: 1; letter-spacing: -0.01em; }
  .brand-swoosh { top: 188px; height: 26px; }
  .product-type { top: 226px; font-size: 14.5px; font-weight: 500; }
  .drop-icon { top: 264px; height: 36px; }
  .eco-figure { top: 304px; font-size: 22px; font-weight: 800; line-height: 1; }
  .eco-label { top: 331px; font-size: 13.5px; font-weight: 500; letter-spacing: 0.02em; }
  .source-line {
    top: 378px; font-family: "Kaushan Script", cursive; line-height: 1;
  }
  .source-line__small { display: block; font-size: 27px; }
  .source-line__large { display: block; font-size: 34px; margin-top: 4px; }
  .mountain-art {
    top: 460px; height: 100px;
    background: linear-gradient(180deg, rgba(255,255,255,0.25) 0%, rgba(255,255,255,0.7) 100%);
  }
  .volume { top: 574px; font-size: 24px; font-weight: 300; line-height: 1; }
  .mineral-note { top: 607px; font-size: 7.5px; font-weight: 600; line-height: 1.5; letter-spacing: 0.02em; }

  .option-band {
    position: absolute; top: 868px; width: 600px; height: 139px; text-align: center;
  }
  .option-band--deep { left: 0; background: var(--deep-blue); }
  .option-band--cyan { left: 600px; background: var(--cyan-blue); }
  .swatches { position: absolute; top: 19px; left: 0; width: 100%; display: flex; justify-content: center; gap: 18px; }
  .swatch { width: 40px; height: 40px; }
  .swatch--outline { border: 2px solid var(--white); }
  .swatch--white { background: var(--white); }
  .option-title { position: absolute; top: 73px; width: 100%; font-size: 18px; font-weight: 700; letter-spacing: 0.12em; }
  .option-colours { position: absolute; top: 100px; width: 100%; font-size: 15.5px; font-weight: 400; letter-spacing: 0.14em; }
</style>
</head>
<body>

  <section class="carton carton--deep">
    <div class="carton__cap"></div>
    <div class="carton__shoulder"></div>
    <div class="carton__panel">
      <p class="tagline">PURE &amp; REFRESHING</p>
      <h1 class="brand-name">Brindle</h1>
      <svg class="brand-swoosh" viewBox="0 0 240 26" preserveAspectRatio="none" aria-hidden="true">
        <path d="M0 20 Q120 -6 240 16 L240 22 Q120 2 0 26 Z" fill="#fff"/>
      </svg>
      <p class="product-type">Natural Spring Water</p>
      <svg class="drop-icon" viewBox="0 0 240 36" aria-hidden="true">
        <path d="M120 2 C126 12 131 19 131 25 A11 11 0 0 1 109 25 C109 19 114 12 120 2 Z" fill="#fff"/>
        <path d="M113 25 A7 7 0 0 0 127 25" fill="none" stroke="#0d3a78" stroke-width="2"/>
      </svg>
      <p class="eco-figure">100%</p>
      <p class="eco-label">ECO-RESPONSIBLE</p>
      <p class="source-line"><span class="source-line__small">Sourced from</span><span class="source-line__large">the Mountains</span></p>
      <div class="mountain-art" role="img" aria-label="Placeholder for white snow-capped mountain range illustration"></div>
      <p class="volume">500ml</p>
      <p class="mineral-note">NATURALLY OCCURRING<br>BALANCED MINERAL CONTENT</p>
    </div>
  </section>

  <section class="carton carton--cyan">
    <div class="carton__cap"></div>
    <div class="carton__shoulder"></div>
    <div class="carton__panel">
      <p class="tagline">PURE &amp; REFRESHING</p>
      <h1 class="brand-name">Brindle</h1>
      <svg class="brand-swoosh" viewBox="0 0 240 26" preserveAspectRatio="none" aria-hidden="true">
        <path d="M0 20 Q120 -6 240 16 L240 22 Q120 2 0 26 Z" fill="#fff"/>
      </svg>
      <p class="product-type">Natural Spring Water</p>
      <svg class="drop-icon" viewBox="0 0 240 36" aria-hidden="true">
        <path d="M120 2 C126 12 131 19 131 25 A11 11 0 0 1 109 25 C109 19 114 12 120 2 Z" fill="#fff"/>
        <path d="M113 25 A7 7 0 0 0 127 25" fill="none" stroke="#0ba2e2" stroke-width="2"/>
      </svg>
      <p class="eco-figure">100%</p>
      <p class="eco-label">ECO-RESPONSIBLE</p>
      <p class="source-line"><span class="source-line__small">Sourced from</span><span class="source-line__large">the Mountains</span></p>
      <div class="mountain-art" role="img" aria-label="Placeholder for white snow-capped mountain range illustration"></div>
      <p class="volume">500ml</p>
      <p class="mineral-note">NATURALLY OCCURRING<br>BALANCED MINERAL CONTENT</p>
    </div>
  </section>

  <section class="option-band option-band--deep">
    <div class="swatches"><span class="swatch swatch--outline"></span><span class="swatch swatch--white"></span></div>
    <p class="option-title">OPTION A</p>
    <p class="option-colours">DEEP BLUE + WHITE</p>
  </section>

  <section class="option-band option-band--cyan">
    <div class="swatches"><span class="swatch swatch--outline"></span><span class="swatch swatch--white"></span></div>
    <p class="option-title">OPTION B</p>
    <p class="option-colours">CYAN BLUE + WHITE</p>
  </section>

</body>
</html>
```